Unique malt liquor beverage needs a logo design and bottle (6.9oz clear glass flask) label designed.

We need a logo and bottle label design for our new beverage here at Lofty Brewworks, a new company based in West Virginia. This is a differentiated product in that we use only natural ingredients and deliver it in a novel 6.9oz glass flask. Our new beverage is a naturally flavored malt liquor drink that we call "Glimmer". Our proposed tag line will be "Made to Glim" or "Cold Sip. Bold Glim". We want a logo and bottle label design that differentiates us even further.

Target Market(s)

See images I uploaded to see our two competitors...we need to be better than this but it gives you idea of the spirit of this beverage class.

Industry/Entity Type

Alcohol beverage

Requirements
Must have
• Label needs to include “14% alc/vol 6.9 oz” Both of these elements can be small and at bottom of front face of label. Also must look great on clear glass flask.
Should not have
• Do not put "malt liquor" on label. Under "Glimmer" name it will need to state "Alcoholic Beverage"

```html
<!DOCTYPE html>
<html lang="en">
<head>
<meta charset="utf-8">
<title>Glimmer Label</title>
<link rel="stylesheet" href="https://fonts.googleapis.com/css2?family=Limelight&family=Playfair+Display:ital@1&family=Cinzel:wght@500&family=Parisienne&family=Oswald:wght@500&family=Josefin+Sans:wght@600&display=swap">
<style>
  :root {
    --page: #f2f2f0;
    --label-green: #00483c;
    --label-band: #003a30;
    --gold: #e8a23c;
    --gold-shadow: #101a14;
    --teal: #1ab8b0;
    --cream: #f4efe6;
    --pattern-tone: rgba(30, 150, 130, 0.22);
    --ornament-tone: rgba(230, 225, 215, 0.35);
  }
  * { margin: 0; padding: 0; box-sizing: border-box; }
  html, body {
    width: 1200px; height: 1200px; overflow: hidden;
    background: var(--page);
  }
  .label {
    position: absolute; left: 282px; top: 100px;
    width: 636px; height: 1000px;
    background: var(--label-green);
    overflow: hidden;
  }
  .label__band { position: absolute; inset: 0; width: 100%; height: 100%; }
  .centered {
    position: absolute; left: 0; width: 100%;
    text-align: center; white-space: nowrap;
  }
  .brand-row {
    top: 110px;
    display: flex; justify-content: center; align-items: center; gap: 16px;
    font-family: "Josefin Sans", sans-serif; font-weight: 600;
    font-size: 24px; letter-spacing: 3px; color: var(--gold);
  }
  .brand-row__dot {
    width: 34px; height: 34px; border-radius: 50%;
    border: 2px solid var(--gold);
  }
  .floral-pattern {
    position: absolute; left: 167px; top: 203px;
    width: 312px; height: 322px; border-radius: 50%;
    background: radial-gradient(circle, var(--pattern-tone) 0%, rgba(30,150,130,0.08) 70%, transparent 72%);
  }
  .product-name {
    top: 340px;
    font-family: "Limelight", serif; font-size: 108px; line-height: 1;
    font-weight: 400;
    color: var(--gold);
    text-shadow: -4px 4px 0 var(--gold-shadow);
    transform: scaleY(1.35);
  }
  .tagline {
    top: 528px;
    font-family: "Playfair Display", serif; font-style: italic;
    font-size: 44px; color: var(--cream);
  }
  .style-name {
    top: 625px;
    font-family: "Cinzel", serif; font-weight: 500;
    font-size: 50px; line-height: 60px; letter-spacing: 3px;
    color: var(--teal);
  }
  .ornament {
    position: absolute; left: 218px; width: 200px; height: 20px;
    background: linear-gradient(90deg, transparent, var(--ornament-tone), transparent);
    border-radius: 10px;
  }
  .ornament--top { top: 772px; }
  .ornament--bottom { top: 866px; }
  .flavor-note {
    top: 798px;
    font-family: "Parisienne", cursive; font-size: 44px; line-height: 60px;
    color: var(--cream);
  }
  .origin {
    top: 900px;
    font-family: "Oswald", sans-serif; font-weight: 500;
    font-size: 30px; line-height: 40px; letter-spacing: 24px; padding-left: 24px;
    color: var(--cream);
  }
  .legal {
    top: 954px;
    font-family: "Oswald", sans-serif; font-weight: 500;
    font-size: 18px; line-height: 24px; letter-spacing: 3px;
    color: var(--cream);
  }
</style>
</head>
<body>
  <main class="label">
    <svg class="label__band" viewBox="0 0 100 100" preserveAspectRatio="none" aria-hidden="true">
      <polygon points="100,6.2 100,52.5 0,91.5 0,49.7" fill="var(--label-band)"/>
    </svg>

    <div class="centered brand-row">
      <span>LOFTY</span>
      <span class="brand-row__dot"></span>
      <span>BREWWORKS</span>
    </div>

    <div class="floral-pattern" role="img" aria-label="Faint line-drawn floral ornament behind the product name"></div>

    <h1 class="centered product-name">Glimmer</h1>
    <p class="centered tagline">Made to Glim</p>
    <p class="centered style-name">ALCOHOLIC<br>BEVERAGE</p>

    <div class="ornament ornament--top" role="img" aria-label="Decorative scroll flourish"></div>
    <p class="centered flavor-note">Naturally Flavored</p>
    <div class="ornament ornament--bottom" role="img" aria-label="Decorative scroll flourish"></div>

    <p class="centered origin">WEST VIRGINIA</p>
    <p class="centered legal">14% ALC/VOL &nbsp;·&nbsp; 6.9 OZ</p>
  </main>
</body>
</html>
```